Private Investment Firm Needs PowerPoint Presentation Template

Design PowerPoint template, take Pinebrook-submitted rough presentation draft, and drop it into new template. See attached Project Brief file for more detail.
Updates

Some decent designs have been submitted but they seem to lack the understanding of our target markets. I am hopeful that more time and feedback will result in better results.

Target Market(s)

Private company owners and intermediaries.

Font styles to use
Serif

Colors
3176b5

Requirements
Must have
• See attached Project Brief.
Nice to have
Should not have
• No B2C fluff--this is a B2B project.

```html
<!DOCTYPE html>
<html lang="en">
<head>
<meta charset="utf-8">
<title>Pinebrook Representative Non-Control Capital Investments</title>
<link href="https://fonts.googleapis.com/css2?family=Montserrat:wght@500;600;700&family=Tinos:wght@400;700&display=swap" rel="stylesheet">
<style>
  :root {
    --brand-blue: #0070c0;
    --ink: #111111;
    --white: #ffffff;
    --accent-red: #c8102e;
    --photo-light: #f7f8f9;
    --photo-mid: #e2e6e9;
  }
  html, body {
    margin: 0;
    padding: 0;
    overflow: hidden;
    background: var(--white);
  }
  .slide {
    position: relative;
    width: 1200px;
    height: 676px;
    overflow: hidden;
    background: var(--white);
    font-family: "Montserrat", Arial, sans-serif;
  }
  .side-rail {
    position: absolute;
    left: 0; top: 0;
    width: 44px; height: 676px;
    background: var(--brand-blue);
  }
  .side-rail-url {
    position: absolute;
    left: 22px; top: 336px;
    transform: translate(-50%, -50%) rotate(-90deg);
    white-space: nowrap;
    font-family: "Tinos", "Times New Roman", serif;
    font-size: 15px;
    letter-spacing: 0.3px;
    color: var(--white);
  }
  .edge-rail {
    position: absolute;
    right: 0; top: 0;
    width: 12px; height: 676px;
    background: var(--brand-blue);
  }
  .page-number {
    position: absolute;
    right: 24px; top: 18px;
    font-family: "Tinos", "Times New Roman", serif;
    font-size: 19px;
    color: var(--ink);
  }
  .slide-title {
    position: absolute;
    left: 86px; top: 82px;
    margin: 0;
    font-size: 27px;
    line-height: 33px;
    font-weight: 700;
    letter-spacing: 0.3px;
    color: var(--brand-blue);
  }
  .architecture-photo {
    position: absolute;
    left: 470px; top: 320px;
    width: 718px; height: 356px;
    background: linear-gradient(100deg, rgba(255,255,255,0) 0%, var(--photo-light) 40%, var(--photo-mid) 75%, var(--photo-light) 100%);
  }
  .case-panel {
    position: absolute;
    left: 45px; top: 231px;
    width: 809px; height: 352px;
    background: var(--brand-blue);
    color: var(--white);
  }
  .case-heading {
    position: absolute;
    left: 41px; top: 44px;
    margin: 0;
    font-size: 40px;
    font-weight: 600;
  }
  .case-points {
    position: absolute;
    left: 41px; top: 124px;
    width: 740px;
    margin: 0; padding: 0;
    list-style: none;
  }
  .case-points li {
    position: relative;
    padding-left: 32px;
    margin-bottom: 28px;
    font-size: 17px;
    font-weight: 500;
    line-height: 28px;
  }
  .case-points li::before {
    content: "";
    position: absolute;
    left: 2px; top: 9px;
    width: 10px; height: 10px;
    background: var(--white);
  }
  .firm-mark {
    position: absolute;
    left: 67px; top: 608px;
    display: flex;
    align-items: center;
    gap: 10px;
  }
  .firm-mark-dot {
    width: 40px; height: 40px;
    border-radius: 50%;
    background: var(--brand-blue);
  }
  .firm-mark-name {
    font-family: "Tinos", "Times New Roman", serif;
    font-size: 17px;
    line-height: 20px;
    letter-spacing: 1.5px;
    color: var(--brand-blue);
  }
  .client-mark {
    position: absolute;
    left: 922px; top: 558px;
    display: flex;
    align-items: center;
    gap: 12px;
  }
  .client-mark-name {
    font-size: 26px;
    line-height: 30px;
    font-weight: 700;
    color: var(--ink);
  }
  .client-mark-dot {
    width: 28px; height: 28px;
    border-radius: 50%;
    background: var(--accent-red);
  }
</style>
</head>
<body>
<div class="slide">
  <div class="side-rail"><span class="side-rail-url">www.pinebrookcap.example</span></div>
  <div class="edge-rail"></div>
  <div class="page-number">17</div>

  <h1 class="slide-title">PINEBROOK REPRESENTATIVE NON-CONTROL<br>CAPITAL INVESTMENTS</h1>

  <div class="architecture-photo" role="img" aria-label="Faint photograph of a white modern building facade with vertical ribs"></div>

  <section class="case-panel">
    <h2 class="case-heading">Family Office Support</h2>
    <ul class="case-points">
      <li>Provides comprehensive and custom packaging for the liquid home cleaning products sector, and has the ability to safely process volatile liquids, such as bleach and hydrogen peroxide.</li>
      <li>Pinebrook’s capital was used to assist a New York-based family office in acquiring the Company as part of their business outsourcing growth strategy thesis.</li>
    </ul>
  </section>

  <div class="firm-mark">
    <span class="firm-mark-dot"></span>
    <span class="firm-mark-name">PINEBROOK<br>CAPITAL</span>
  </div>

  <div class="client-mark">
    <span class="client-mark-name">Quillane<br>Corporation</span>
    <span class="client-mark-dot"></span>
  </div>
</div>
</body>
</html>
```